Business card design for sustainable building and development company

Need a business card design for a new sustainable building and real estate development company in the San Francisco Bay area. Name of company is "Tovrin Advisors, LLC" and we provide "Sustainable building, energy and development services" for residential and non residential projects. We'd like the following colors used but not all area required: green, gray, blue. Design should communicate innovation, professionalism and sustainability. Our current website is www.tovrin-advisors.example. Another possible design idea is to have the following listed on the back of the card:
Certified: VERN QS, Eco Marker Rater, DOLM Rater, Terravue Inspector, KSO TQ Building Analyst. Its not a must but could be text that could be used for back of card. Overall, we are open to a simple, clean design and or one with more text than usual for a card.

Industry/Entity Type

Real Estate

Contact Information for Business Card

Name on card: Mark J. Halvik
Title for Name: Principal + Founder
Phone: 555.814.0627
Email: mhalvik@tovrin-advisors.example
Website: www.tovrin-advisors.example

Also, please add the following for address:
Halden Bay, Westmark

Requirements
Nice to have
• If you can integrate the outline of a skyline on the backside of the card and if it looks good, I would like to see the design
Should not have
• a barcode;

```html
<!DOCTYPE html>
<html lang="en">
<head>
<meta charset="utf-8">
<title>Tovrin Advisors — Business Card</title>
<link href="https://fonts.googleapis.com/css2?family=Montserrat:wght@300;400;600;700&display=swap" rel="stylesheet">
<style>
  :root {
    --backdrop: #6b6b6b;
    --card: #f4f4f2;
    --band: #1c1c1c;
    --band-text: #9a9a9a;
    --green: #5fb12f;
    --ink: #2a2a2a;
  }
  * { box-sizing: border-box; margin: 0; padding: 0; }
  html, body { width: 1200px; height: 1029px; overflow: hidden; }
  body {
    background: var(--backdrop);
    font-family: "Montserrat", sans-serif;
    position: relative;
  }
  .card {
    position: absolute;
    left: 190px;
    width: 820px;
    height: 440px;
    background: var(--card);
    box-shadow: 0 10px 30px rgba(0,0,0,.35);
    overflow: hidden;
  }
  .card--front { top: 55px; }
  .card--back { top: 535px; }
  .band {
    position: absolute;
    left: 0; right: 0; bottom: 0;
    height: 100px;
    background: var(--band);
    display: flex;
    align-items: center;
    justify-content: center;
  }
  .band__web {
    color: var(--band-text);
    font-size: 13px;
    letter-spacing: .5px;
    font-weight: 400;
  }
  .brand {
    position: absolute;
    display: flex;
    align-items: center;
    gap: 14px;
  }
  .card--front .brand { left: 175px; top: 110px; }
  .card--back .brand { left: 50px; top: 70px; transform: scale(.82); transform-origin: left top; }
  .brand__dot {
    width: 96px; height: 96px;
    border-radius: 50%;
    background: var(--green);
    flex: none;
  }
  .brand__name {
    color: var(--green);
    font-weight: 700;
    font-size: 44px;
    line-height: 1;
  }
  .brand__tagline {
    margin-top: 8px;
    font-size: 11.5px;
    font-weight: 600;
    color: var(--ink);
    text-transform: uppercase;
    letter-spacing: .2px;
  }
  .contact {
    position: absolute;
    left: 400px;
    top: 150px;
    color: var(--ink);
  }
  .contact__name {
    font-size: 24px;
    text-transform: uppercase;
    letter-spacing: .5px;
  }
  .contact__name b { font-weight: 700; }
  .contact__name span { font-weight: 300; }
  .contact__title {
    font-size: 10px;
    font-weight: 600;
    margin-top: 4px;
    text-transform: uppercase;
  }
  .contact__list { list-style: none; margin-top: 16px; }
  .contact__list li {
    display: flex;
    align-items: center;
    gap: 10px;
    font-size: 13px;
    font-weight: 600;
    text-transform: uppercase;
    height: 24px;
  }
  .contact__list svg { width: 14px; height: 14px; fill: var(--green); flex: none; }
  .contact__sep { color: var(--ink); font-weight: 600; }
</style>
</head>
<body>

<section class="card card--front" aria-label="Card front">
  <div class="brand">
    <div class="brand__dot"></div>
    <div>
      <div class="brand__name">Tovrin Advisors</div>
      <div class="brand__tagline">Sustainable building, energy &amp; development services</div>
    </div>
  </div>
  <div class="band"><span class="band__web">WWW.TOVRIN-ADVISORS.EXAMPLE</span></div>
</section>

<section class="card card--back" aria-label="Card back">
  <div class="brand">
    <div class="brand__dot"></div>
    <div>
      <div class="brand__name">Tovrin Advisors</div>
      <div class="brand__tagline">Sustainable building, energy &amp; development services</div>
    </div>
  </div>

  <div class="contact">
    <div class="contact__name"><b>Mark J.</b> <span>Halvik</span> <b>, VERN QS</b></div>
    <div class="contact__title">Principle/Owner</div>
    <ul class="contact__list">
      <li>
        <svg viewBox="0 0 24 24" aria-hidden="true"><path d="M6.6 10.8c1.4 2.8 3.8 5.1 6.6 6.6l2.2-2.2c.3-.3.7-.4 1-.2 1.1.4 2.3.6 3.6.6.6 0 1 .4 1 1V20c0 .6-.4 1-1 1C10.6 21 3 13.4 3 4c0-.6.4-1 1-1h3.5c.6 0 1 .4 1 1 0 1.3.2 2.5.6 3.6.1.3 0 .7-.2 1z"/></svg>
        <span class="contact__sep">:</span> 555.814.0627
      </li>
      <li>
        <svg viewBox="0 0 24 24" aria-hidden="true"><path d="M2 5h20v2l-10 7L2 7z M2 9l10 7 10-7v10H2z"/></svg>
        <span class="contact__sep">:</span> mhalvik@tovrin-advisors.example
      </li>
      <li>
        <svg viewBox="0 0 24 24" aria-hidden="true"><circle cx="12" cy="12" r="10"/></svg>
        <span class="contact__sep">:</span> www.tovrin-advisors.example
      </li>
      <li>
        <svg viewBox="0 0 24 24" aria-hidden="true"><path d="M12 2a7 7 0 0 0-7 7c0 5 7 13 7 13s7-8 7-13a7 7 0 0 0-7-7zm0 9.5A2.5 2.5 0 1 1 12 6.5a2.5 2.5 0 0 1 0 5z"/></svg>
        <span class="contact__sep">:</span> Halden Bay, Westmark
      </li>
    </ul>
  </div>

  <div class="band"></div>
</section>

</body>
</html>
```